German Headhunter/ HR Consultancy needs Business Cards Design

We need a business Card Design for our Company in Stuttgart. We are specialized as Headhunter/ HR Consultancy in Placement of specialist and managers in permanent employment. Please refer to our business logo.

```html
<!DOCTYPE html>
<html lang="de">
<head>
<meta charset="utf-8">
<title>Halden Personalberatung – Business Card</title>
<link rel="stylesheet" href="https://fonts.googleapis.com/css2?family=Arimo:wght@400;700&display=swap">
<style>
  :root {
    --page-bg: #d8d1c6;
    --navy-deep: #111a44;
    --navy: #1c2c6e;
    --royal: #2b45a8;
    --cream: #ece2cf;
    --gold: #b89c74;
    --sand-light: #eadcc4;
    --sand-mid: #c7b08f;
    --sand-dark: #a98f6e;
  }
  * { box-sizing: border-box; margin: 0; padding: 0; }
  html, body {
    width: 1200px;
    height: 927px;
    overflow: hidden;
    background: var(--page-bg);
    font-family: "Arimo", Arial, sans-serif;
  }
  .business-card {
    position: absolute;
    left: 50px;
    top: 157px;
    width: 1100px;
    height: 613px;
    overflow: hidden;
    background:
      radial-gradient(ellipse 320px 420px at 700px 500px, rgba(52, 84, 200, 0.75), transparent 70%),
      radial-gradient(ellipse 300px 380px at 330px 260px, rgba(44, 70, 180, 0.6), transparent 70%),
      linear-gradient(180deg, var(--navy) 0%, var(--navy) 70%, var(--navy-deep) 100%);
    box-shadow: 0 10px 30px rgba(0, 0, 0, 0.25);
  }
  .brand-mark-area {
    position: absolute;
    left: 0;
    top: 0;
    width: 1100px;
    height: 613px;
  }
  .wordmark {
    position: absolute;
    left: 74px;
    top: 72px;
    display: flex;
    align-items: center;
    gap: 28px;
    color: var(--cream);
  }
  .wordmark-square {
    width: 22px;
    height: 22px;
    background: var(--cream);
  }
  .wordmark-name {
    display: block;
    font-weight: 700;
    font-size: 62px;
    line-height: 1;
    letter-spacing: 1px;
  }
  .wordmark-sub {
    display: block;
    font-weight: 700;
    font-size: 27px;
    line-height: 1.3;
    letter-spacing: 0.3px;
  }
  .person-name {
    position: absolute;
    left: 74px;
    top: 226px;
    font-weight: 700;
    font-size: 39px;
    line-height: 44px;
    color: var(--cream);
    letter-spacing: 0.5px;
  }
  .person-role {
    position: absolute;
    left: 74px;
    top: 272px;
    font-size: 28px;
    line-height: 32px;
    color: var(--cream);
  }
  .address {
    position: absolute;
    left: 74px;
    top: 331px;
    font-size: 28px;
    line-height: 36px;
    color: var(--cream);
    font-style: normal;
  }
  .contact-list {
    position: absolute;
    left: 74px;
    top: 424px;
    list-style: none;
  }
  .contact-item {
    display: flex;
    align-items: center;
    height: 43px;
    font-size: 29px;
    color: var(--gold);
  }
  .contact-icon {
    width: 26px;
    height: 26px;
    margin-right: 16px;
    fill: var(--gold);
  }
</style>
</head>
<body>
  <section class="business-card">
    <svg class="brand-mark-area" viewBox="0 0 1100 613" role="img" aria-label="Large brand mark decoration in sand and navy tones">
      <defs>
        <linearGradient id="sand-fill" x1="0" y1="0" x2="1" y2="1">
          <stop offset="0" stop-color="#eadcc4"/>
          <stop offset="0.5" stop-color="#c7b08f"/>
          <stop offset="1" stop-color="#a98f6e"/>
        </linearGradient>
      </defs>
      <polygon points="922,0 1100,0 1100,613 922,613 611,313" fill="url(#sand-fill)" opacity="0.92"/>
    </svg>

    <div class="wordmark">
      <span class="wordmark-square"></span>
      <div>
        <span class="wordmark-name">HALDEN</span>
        <span class="wordmark-sub">PERSONALBERATUNG</span>
      </div>
    </div>

    <h1 class="person-name">MARKUS WEBER</h1>
    <p class="person-role">Manager</p>

    <address class="address">Königstraße 48, Stuttgart<br>BW, 70173</address>

    <ul class="contact-list">
      <li class="contact-item">
        <svg class="contact-icon" viewBox="0 0 24 24" aria-hidden="true">
          <path d="M6.6 10.8a15.1 15.1 0 0 0 6.6 6.6l2.2-2.2c.3-.3.7-.4 1-.2 1.1.4 2.3.6 3.6.6.6 0 1 .4 1 1V20c0 .6-.4 1-1 1C10.6 21 3 13.4 3 4c0-.6.4-1 1-1h3.5c.6 0 1 .4 1 1 0 1.3.2 2.5.6 3.6.1.3 0 .7-.2 1z"/>
        </svg>
        0711-555-2100
      </li>
      <li class="contact-item">
        <svg class="contact-icon" viewBox="0 0 24 24" aria-hidden="true">
          <path d="M2 5h20v14H2z M2 5l10 8 10-8" fill="none" stroke="#b89c74" stroke-width="2"/>
        </svg>
        kontakt@halden-pb.de
      </li>
      <li class="contact-item">
        <svg class="contact-icon" viewBox="0 0 24 24" aria-hidden="true">
          <circle cx="12" cy="12" r="10" fill="none" stroke="#b89c74" stroke-width="2"/>
          <path d="M2 12h20M12 2c3 3 3 17 0 20M12 2c-3 3-3 17 0 20" fill="none" stroke="#b89c74" stroke-width="1.6"/>
        </svg>
        www.halden-pb.de
      </li>
    </ul>
  </section>
</body>
</html>
```